Redesign This Psychology Website

We would like a slight redesign of this successful psychology (relationship counselling) website:

www.TheKelvaleClinic.com.au

We are updating the website, and we'd like a slight refresh of the design and style.

Please keep to very similar colours, and use the same logo. We're looking for around 10 page templates, however the main one is the home page.

Keep in mind, this website already converts quite well, so we want a new, fresh design in keeping with this one. Please don't bother designing something too extremely different.

thanks :)

Target Market(s)

couples who are looking for relationship counselling. Men and women, 25 - 70, across Australia

Industry/Entity Type

Psychology

Number of Pages Required

5+ page

Font styles to use
Sans Serif

Colors
87cfc6
b7a5cd
ec1f27
ffffff
cee9f5

Requirements
Must have
• a similar look to the current design, just looking for a slight refresh.
• Search bar
• Areas for lots of photos
• same logo
• lots of content areas
Nice to have
• great content areas, where we can display a lot of content and our areas.
Should not have
• no colors like orange, etc.
• should not have a totally different feel.

```html
<!DOCTYPE html>
<html lang="en">
<head>
<meta charset="utf-8">
<title>The Kelvale Clinic – Relationship &amp; Marriage Counselling</title>
<link rel="stylesheet" href="https://fonts.googleapis.com/css2?family=Lato:wght@300;400;700&display=swap">
<style>
:root{
  --teal:#87cfc6;
  --teal-dark:#5fb8ad;
  --teal-text:#6fc4ba;
  --link:#2c8f98;
  --ink:#333;
  --muted:#666;
  --grey-bg:#f6f6f6;
  --nav-bg:#f2f2f2;
  --line:#dcdcdc;
  --white:#fff;
}
*{box-sizing:border-box;margin:0;padding:0}
html,body{width:1200px;height:2568px;overflow:hidden;background:var(--white)}
body{font-family:'Lato',Arial,sans-serif;color:var(--ink);position:relative}
.abs{position:absolute}

/* header */
.site-header{position:absolute;left:0;top:0;width:1200px;height:125px;background:var(--white)}
.brand{position:absolute;left:99px;top:30px;display:flex;align-items:center;gap:12px}
.brand-dot{width:52px;height:52px;border-radius:50%;background:var(--teal)}
.brand-name{font-size:33px;font-weight:400;color:var(--link);line-height:1}
.brand-tag{position:absolute;left:163px;top:88px;font-size:14px;color:var(--teal-dark)}
.call{position:absolute;left:526px;top:50px;display:flex;align-items:center;gap:10px}
.call-icon{width:40px;height:40px;border:2px solid var(--teal);border-radius:50%;display:flex;align-items:center;justify-content:center}
.call-label{font-size:11px;color:var(--muted);letter-spacing:.5px}
.call-number{font-size:23px;color:var(--teal-dark);font-weight:400;line-height:1.1}
.search{position:absolute;left:758px;top:56px;width:343px;height:33px;border:1px solid #e2e2e2;display:flex;align-items:center;justify-content:space-between;padding:0 12px;font-size:11px;color:#888}

/* nav */
.main-nav{position:absolute;left:0;top:125px;width:1200px;height:43px;background:var(--nav-bg)}
.main-nav ul{position:absolute;left:99px;top:0;height:43px;display:flex;list-style:none}
.main-nav li{height:43px;display:flex;align-items:center;padding:0 12px;font-size:13px;color:#555;border-right:1px solid var(--line);text-transform:uppercase}
.main-nav li:last-child{border-right:none}
.main-nav li.active{background:var(--teal);color:var(--white);padding:0 14px}

/* hero */
.hero{position:absolute;left:0;top:168px;width:1200px;height:491px;background:linear-gradient(90deg,#cfc2b8 0%,#e4ddd8 20%,#ece8e6 45%,#d9d4d2 65%,#e9e9eb 100%)}
.hero-title{position:absolute;left:0;top:228px;width:1200px;text-align:center;font-size:58px;font-weight:300;color:var(--white)}
.hero-arrow{position:absolute;top:230px}
.finder{position:absolute;left:118px;top:358px;width:962px;height:133px;background:rgba(255,255,255,.85)}
.finder-field{position:absolute;top:42px;width:183px}
.finder-field label{display:block;font-size:13px;color:#444;margin-bottom:6px}
.finder-select{height:36px;border:1px solid #ddd;background:var(--white);display:flex;align-items:center;justify-content:space-between;padding:0 12px;font-size:13px;color:#999}
.btn{display:flex;align-items:center;justify-content:center;background:var(--teal);color:var(--white);text-transform:uppercase;font-size:17px;letter-spacing:.3px}
.finder .btn{position:absolute;left:733px;top:58px;width:147px;height:38px;font-size:17px}

/* intro */
.intro-title{position:absolute;left:0;top:718px;width:1200px;text-align:center;font-size:34px;font-weight:400;color:var(--teal-text)}
.intro-text{position:absolute;left:150px;top:780px;width:900px;text-align:center;font-size:17.5px;line-height:24px;color:var(--muted)}
.intro-text p+p{margin-top:30px}
.intro .btn{position:absolute;left:445px;top:957px;width:310px;height:50px}

/* services */
.services{position:absolute;left:0;top:1092px;width:1200px;height:658px;background:var(--grey-bg)}
.section-title{position:absolute;left:0;width:1200px;text-align:center;font-size:34px;font-weight:300;color:#555;text-transform:uppercase}
.card{position:absolute;top:144px;width:233px;height:332px;background:var(--white)}
.card-photo{height:180px}
.card h3{font-size:20px;font-weight:400;line-height:22px;color:#222;margin:22px 12px 0}
.card time{display:block;font-size:12px;color:#444;margin:10px 12px 0}
.card .more{display:block;font-size:14px;font-weight:700;color:var(--link);margin:14px 12px 0}
.btn-outline{position:absolute;left:519px;top:546px;width:161px;height:40px;border:1px solid var(--link);color:var(--link);background:var(--white);display:flex;align-items:center;justify-content:center;font-size:17px}

/* video */
.video-lead{position:absolute;left:99px;top:1892px;font-size:18.5px;font-weight:700;color:var(--teal-text)}
.video-text{position:absolute;left:99px;top:1930px;width:520px;font-size:13px;line-height:22px;color:#444}
.video-text p+p{margin-top:8px}
.video-section .btn{position:absolute;left:99px;top:2106px;width:233px;height:48px;font-size:18px}
.player{position:absolute;left:669px;top:1880px;width:435px;height:274px;background:var(--white);border:1px solid #ddd;box-shadow:0 1px 4px rgba(0,0,0,.15);padding:12px}
.player-screen{height:228px;background:linear-gradient(160deg,#fff3c4 0%,#e8c870 30%,#9a8a4c 65%,#5a5a3c 100%);position:relative}
.player-bar{height:28px;background:#2c2c2c;display:flex;align-items:center;gap:10px;padding:0 10px}
.player-track{flex:1;height:5px;background:#eee;border-radius:3px;position:relative}
.player-track span{position:absolute;left:0;top:0;height:5px;width:44%;background:#3d86c6;border-radius:3px}

/* footer */
.site-footer{position:absolute;left:0;top:2239px;width:1200px;height:329px;background:var(--teal);color:#1d3e3b}
.footer-col{position:absolute;top:42px}
.footer-col h4{font-size:17px;font-weight:400;text-transform:uppercase;margin-bottom:18px}
.footer-col li{list-style:none;font-size:13.5px;line-height:30px}
.footer-divider{position:absolute;top:40px;width:1px;height:160px;background:rgba(0,0,0,.08)}
.contact-line{display:flex;align-items:center;gap:10px;font-size:13.5px;line-height:30px}
.socials{display:flex;gap:5px;margin-top:12px}
.socials span{width:36px;height:36px;border-radius:50%;border:2px solid var(--white);background:#3a8fc9}
.socials span:nth-child(2){background:#3b5ea3}
.socials span:nth-child(3){background:#1f6fa3}
.socials span:nth-child(4){background:#d0463a}
.footer-rule{position:absolute;left:99px;top:254px;width:1002px;height:1px;background:rgba(0,0,0,.12)}
.copyright{position:absolute;left:99px;top:278px;font-size:12px}
.page-code{position:absolute;right:99px;top:278px;font-size:13px}
</style>
</head>
<body>

<header class="site-header">
  <div class="brand"><span class="brand-dot"></span><span class="brand-name">The Kelvale Clinic</span></div>
  <div class="brand-tag">helping you create loving relationships</div>
  <div class="call">
    <span class="call-icon"><svg width="20" height="20" viewBox="0 0 24 24"><path d="M6.6 10.8a15.1 15.1 0 0 0 6.6 6.6l2.2-2.2a1 1 0 0 1 1-.25 11.4 11.4 0 0 0 3.6.57 1 1 0 0 1 1 1V20a1 1 0 0 1-1 1A17 17 0 0 1 3 4a1 1 0 0 1 1-1h3.5a1 1 0 0 1 1 1c0 1.25.2 2.45.57 3.57a1 1 0 0 1-.25 1z" fill="#87cfc6"/></svg></span>
    <div><div class="call-label">CALL US ON:</div><div class="call-number">1300 555 018</div></div>
  </div>
  <div class="search"><span>Relationship Information Topic</span>
    <svg width="13" height="13" viewBox="0 0 24 24"><circle cx="10" cy="10" r="7" fill="none" stroke="#87cfc6" stroke-width="3"/><path d="M15 15l6 6" stroke="#87cfc6" stroke-width="3"/></svg></div>
</header>

<nav class="main-nav">
  <ul>
    <li class="active">Home</li><li>About</li><li>Counselling Types</li><li>Relationship Counselling Locations</li><li>Sex Therapy Locations</li><li>Quizzes</li><li>F.A.Q.'s</li><li>Contact</li>
  </ul>
</nav>

<section class="hero">
  <div class="abs" style="left:0;top:0;width:1200px;height:491px" role="img" aria-label="Photo of a smiling couple embracing"></div>
  <svg class="hero-arrow" style="left:38px" width="18" height="36" viewBox="0 0 18 36"><path d="M15 2L3 18l12 16" fill="none" stroke="#fff" stroke-width="2"/></svg>
  <svg class="hero-arrow" style="left:1118px;top:228px" width="46" height="46" viewBox="0 0 46 46"><circle cx="23" cy="23" r="22" fill="rgba(0,0,0,.12)"/><path d="M19 13l10 10-10 10" fill="none" stroke="#fff" stroke-width="2"/></svg>
  <h1 class="hero-title">Find Our Psychologist Near You</h1>
  <form class="finder">
    <div class="finder-field" style="left:82px"><label>Type of Counselling</label><div class="finder-select">Select<svg width="10" height="6" viewBox="0 0 10 6"><path d="M1 1l4 4 4-4" fill="none" stroke="#999"/></svg></div></div>
    <div class="finder-field" style="left:296px"><label>Location</label><div class="finder-select">Select<svg width="10" height="6" viewBox="0 0 10 6"><path d="M1 1l4 4 4-4" fill="none" stroke="#999"/></svg></div></div>
    <div class="finder-field" style="left:510px"><label>Post code</label><div class="finder-select">Select<svg width="10" height="6" viewBox="0 0 10 6"><path d="M1 1l4 4 4-4" fill="none" stroke="#999"/></svg></div></div>
    <div class="btn">Search Now</div>
  </form>
</section>

<section class="intro">
  <h2 class="intro-title">We Specialise in Relationship &amp; Marriage Counselling</h2>
  <div class="intro-text">
    <p>At the Kelvale Clinic, we are a group of PSYCHOLOGISTS, Australia wide who are passionate about relationships and helping you with yours.</p>
    <p>Our vision is to provide the most highly regarded and comprehensive marriage counselling and relationship counselling, and sex therapy in Australia, at reasonable and affordable rates.</p>
  </div>
  <div class="btn">Read More Information</div>
</section>

<section class="services">
  <h2 class="section-title" style="top:62px">Our Services</h2>
  <article class="card" style="left:99px"><div class="card-photo" role="img" aria-label="Photo of a smiling middle-aged couple" style="background:linear-gradient(135deg,#d9dde2,#b9c4cf)"></div><h3>What can I do if I'm living with a Narcissist?</h3><time>February 24, 2017</time><span class="more">Read more »</span></article>
  <article class="card" style="left:356px"><div class="card-photo" role="img" aria-label="Photo of a woman talking with a counsellor" style="background:linear-gradient(135deg,#e5e7ea,#c9a2b8)"></div><h3>Why am I with a Narcissist?</h3><time>February 24, 2017</time><span class="more">Read more »</span></article>
  <article class="card" style="left:611px"><div class="card-photo" role="img" aria-label="Photo of a happy couple at the beach" style="background:linear-gradient(135deg,#9fd4ec,#e8cfa8)"></div><h3>How Do I Know If I'm With a Narcissist?</h3><time>February 24, 2017</time><span class="more">Read more »</span></article>
  <article class="card" style="left:868px"><div class="card-photo" role="img" aria-label="Photo of a counselling session with notes" style="background:linear-gradient(135deg,#b9aaa3,#5d4f4d)"></div><h3>Are You Living With a Steamroller?</h3><time>February 24, 2017</time><span class="more">Read more »</span></article>
  <div class="btn-outline">VIEW MORE</div>
</section>

<section class="video-section">
  <h2 class="section-title" style="top:1803px">Our Video</h2>
  <h3 class="video-lead">Communication is a vital skill but not often taught to us</h3>
  <div class="video-text">
    <p>Most people find that their ways of communicating with each other are what hamper us from having a happy healthy relationship.</p>
    <p>Effective Interpersonal Communication skills are not something that we are usually taught. But for almost everyone who is having difficulties in their relationship, they feel that they are trying to communicate their thoughts and feelings but that their partner is not listening.</p>
  </div>
  <div class="btn">More Information</div>
  <div class="player">
    <div class="player-screen" role="img" aria-label="Video still of a couple walking among sunlit trees">
      <svg class="abs" style="left:180px;top:84px" width="60" height="60" viewBox="0 0 60 60"><circle cx="30" cy="30" r="27" fill="none" stroke="#fff" stroke-width="3"/><path d="M24 18l18 12-18 12z" fill="none" stroke="#fff" stroke-width="3"/></svg>
    </div>
    <div class="player-bar">
      <svg width="10" height="12" viewBox="0 0 10 12"><path d="M0 0l10 6-10 6z" fill="#fff"/></svg>
      <div class="player-track"><span></span></div>
      <svg width="16" height="12" viewBox="0 0 16 12"><path d="M0 4h3l4-4v12l-4-4H0z" fill="#fff"/><path d="M10 3a4 4 0 0 1 0 6M12 1a7 7 0 0 1 0 10" fill="none" stroke="#fff"/></svg>
    </div>
  </div>
</section>

<footer class="site-footer">
  <div class="footer-col" style="left:99px"><h4>Quick Links</h4><ul><li>Home</li><li>About</li><li>Resources</li><li>Blog</li><li>Contact</li></ul></div>
  <div class="footer-col" style="left:236px;top:77px"><ul><li>Privacy Policy</li><li>Terms &amp; Conditions</li><li>Site Map</li><li>Associate Psychologists Program</li></ul></div>
  <div class="footer-divider" style="left:467px"></div>
  <div class="footer-col" style="left:515px"><h4>Get In Touch</h4>
    <div class="contact-line"><svg width="12" height="12" viewBox="0 0 24 24"><path d="M6.6 10.8a15.1 15.1 0 0 0 6.6 6.6l2.2-2.2a1 1 0 0 1 1-.25 11.4 11.4 0 0 0 3.6.57 1 1 0 0 1 1 1V20a1 1 0 0 1-1 1A17 17 0 0 1 3 4a1 1 0 0 1 1-1h3.5a1 1 0 0 1 1 1c0 1.25.2 2.45.57 3.57a1 1 0 0 1-.25 1z" fill="#1d3e3b"/></svg>Call us on &nbsp;1300 555 018</div>
    <div class="contact-line"><svg width="13" height="10" viewBox="0 0 13 10"><rect width="13" height="10" fill="#1d3e3b"/><path d="M0 0l6.5 5L13 0" fill="none" stroke="#87cfc6"/></svg>info@kelvaleclinic.com.au</div>
  </div>
  <div class="footer-divider" style="left:710px"></div>
  <div class="footer-col" style="left:777px"><h4>Why Us</h4><ul><li>Customers</li><li>Team</li><li>FAQ</li><li>Contact</li></ul></div>
  <div class="footer-divider" style="left:908px"></div>
  <div class="footer-col" style="left:942px"><h4>Follow Us</h4><div style="font-size:13.5px">Please connect with us on</div>
    <div class="socials"><span></span><span></span><span></span><span></span></div></div>
  <div class="footer-rule"></div>
  <div class="copyright">© 2017 The Kelvale Clinic. &nbsp;All right reserved &nbsp;Term of Use</div>
  <div class="page-code">C16</div>
</footer>

</body>
</html>
```